Brookvane Consulting Business Card Design

Business Card Design for Brookvane Consulting. Brookvane Consulting is a boutique consultancy based in Atlanta, GA., that specializes in marketing strategy, organization planning, and leadership development. We provide solutions for small businesses and startups as well as Vantage 300 companies.

http://brookvaneconsulting.com/

Target Market(s)

We provide solutions for small businesses and startups as well as Vantage 300 companies.

Industry/Entity Type

Consulting

Contact Information for Business Card

Two sided business card with priority on contact information, logo, tag line (Guidance to Think Bigger, Act Sooner, Grow Further)

Colors

Designer to choose colors to be used in the design.

Requirements
Must have
• contact information, logo, tag line (Guidance to Think Bigger, Act Sooner, Grow Further)
• Simple no over communication.
Nice to have
• I would like to see different placements of logo and creative use of both sides of the card
Should not have
• Do not put too much information on the card.

```html
<!DOCTYPE html>
<html lang="en">
<head>
<meta charset="utf-8">
<title>Brookvane Consulting Business Card</title>
<link rel="stylesheet" href="https://fonts.googleapis.com/css2?family=Lato:wght@300;400;700&family=Kaushan+Script&display=swap">
<style>
  :root {
    --backdrop: #3b3532;
    --card-grey: #c6c6c6;
    --card-black: #161616;
    --ink: #1a1a1a;
    --ink-soft: #2c2c2c;
    --paper-white: #f7f7f7;
    --tagline: #d8d8d8;
  }
  html, body {
    margin: 0;
    padding: 0;
    overflow: hidden;
  }
  .canvas {
    position: relative;
    width: 1200px;
    height: 769px;
    background: var(--backdrop);
    overflow: hidden;
    font-family: "Lato", sans-serif;
  }
  .card {
    position: absolute;
    top: 234px;
    width: 520px;
    height: 300px;
    border-radius: 3px;
    overflow: hidden;
    box-shadow: 0 10px 24px rgba(0,0,0,0.35);
  }
  /* Contact side */
  .card-contact {
    left: 50px;
    background: var(--card-grey);
    color: var(--ink);
  }
  .mark-area {
    position: absolute;
    left: 0;
    bottom: 0;
    width: 190px;
    height: 170px;
    background: var(--paper-white);
  }
  .holder {
    position: absolute;
    top: 42px;
    left: 200px;
    width: 280px;
    text-align: center;
  }
  .holder-name {
    font-family: "Kaushan Script", cursive;
    font-size: 30px;
    line-height: 1.1;
    margin: 0;
  }
  .holder-role {
    font-size: 15px;
    margin: 4px 0 0;
    color: var(--ink-soft);
  }
  .contact-list {
    position: absolute;
    right: 30px;
    top: 168px;
    text-align: right;
    font-size: 15px;
    line-height: 1.3;
    color: var(--ink-soft);
    margin: 0;
    padding: 0;
    list-style: none;
  }
  .contact-list .label {
    font-weight: 700;
  }
  /* Brand side */
  .card-brand {
    left: 630px;
    background: var(--card-black);
    color: #ffffff;
  }
  .brand-lockup {
    position: absolute;
    top: 92px;
    left: 0;
    width: 100%;
    display: flex;
    justify-content: center;
    align-items: center;
    gap: 12px;
  }
  .brand-square {
    width: 18px;
    height: 18px;
    background: #ffffff;
  }
  .brand-name {
    font-size: 38px;
    font-weight: 400;
    letter-spacing: 1px;
    margin: 0;
  }
  .tagline {
    position: absolute;
    top: 186px;
    width: 100%;
    text-align: center;
    font-size: 15px;
    color: var(--tagline);
    margin: 0;
  }
</style>
</head>
<body>
<main class="canvas">
  <section class="card card-contact" aria-label="Contact side">
    <div class="mark-area" role="img" aria-label="Brand symbol decoration area"></div>
    <div class="holder">
      <h1 class="holder-name">Darnell Whitford</h1>
      <p class="holder-role">Founder/Managing Director</p>
    </div>
    <ul class="contact-list">
      <li><span class="label">PHONE:</span> 404-555-0187</li>
      <li>darnell@brookvaneconsulting.com</li>
      <li>brookvaneconsulting.com</li>
    </ul>
  </section>

  <section class="card card-brand" aria-label="Brand side">
    <div class="brand-lockup">
      <span class="brand-square" aria-hidden="true"></span>
      <h2 class="brand-name">Brookvane Consulting</h2>
    </div>
    <p class="tagline">Guidance to Think Bigger, Act Sooner, Grow Further</p>
  </section>
</main>
</body>
</html>
```